Brightwell Practice Partners, Inc (www.brightwellpracticepartnrs.example) would like to design a website to convey a level of professionalism to healthcare providers that we are the place form them to visit for Contin. Education, Marketing and Management, Joint Venture Partnerships, etc.
We think we would like a WP Site so that we can use the dynamic and static sides of it's capabilities. We also want to have something that acts as a membership side where members can post their Bio and CV's and prospective employers can post help wanted ads.

Target Market(s)

Pediatricians, Pediatric Dentist, Employers seeking these doctors

Industry/Entity Type

Healthcare

Requirements
Must have
• Services:
Resumes/Bio
Help Wanted
Continuing Education Programs
Marketing & Management

```html
<!DOCTYPE html>
<html lang="en">
<head>
<meta charset="utf-8">
<title>BPP – Brightwell Practice Partners</title>
<link href="https://fonts.googleapis.com/css2?family=Lato:wght@400;700&family=PT+Sans+Narrow&display=swap" rel="stylesheet">
<style>
:root{
  --navy:#1d5a7a; --teal:#3e7d98; --teal-dark:#2a5f78; --sky:#dcebf3; --sky2:#f3f8fb;
  --text:#333; --muted:#666; --link:#2d78a6; --orange:#f29a12; --red:#d81f26; --line:#d6dee3;
}
*{box-sizing:border-box;margin:0;padding:0}
html,body{width:961px;height:1200px;overflow:hidden;background:#fff;font-family:"Lato",sans-serif;color:var(--text)}
.page{position:relative;width:961px;height:1200px}
.abs{position:absolute}
.header{left:0;top:0;width:961px;height:74px;background:linear-gradient(#eaf3f8,#cfe2ec);border-top:2px solid var(--teal)}
.logo{left:130px;top:22px;font-size:27px;color:var(--navy);letter-spacing:1px}
.topbar{left:598px;top:11px;font-size:10px;color:#333;display:flex;gap:10px;align-items:center}
.topbar .phone{color:var(--navy);font-size:11px}
.topbar .sep{border-left:1px solid #aab;height:14px}
.search{left:688px;top:40px;width:138px;height:19px;border:1px solid #9bb;background:#fff;font-size:9px;color:#888;display:flex;align-items:center}
.search i{width:17px;height:17px;background:var(--teal);margin-right:6px;display:flex;align-items:center;justify-content:center}
.nav{left:0;top:74px;width:961px;height:22px;background:linear-gradient(#5d98b3,#356f8b);box-shadow:0 3px 4px rgba(0,0,0,.25)}
.nav a{position:absolute;top:5px;font-size:10px;color:#fff;text-decoration:none;transform:translateX(-50%);white-space:nowrap}
.nav .div{position:absolute;top:0;width:1px;height:22px;background:#2b5a72}
.hero{left:130px;top:107px;width:700px;height:307px;background:linear-gradient(110deg,#c9a77e 0%,#eee9e1 35%,#f4efe8 60%,#b9aa92 100%);box-shadow:0 1px 4px rgba(0,0,0,.35)}
.arrow{top:237px;width:28px;height:30px;background:#fff;display:flex;align-items:center;justify-content:center;box-shadow:0 1px 3px rgba(0,0,0,.3)}
.register{left:587px;top:341px;width:232px;height:242px;background:var(--teal-dark);border-radius:6px 6px 0 0;color:#fff}
.register h2{font-weight:400;font-size:14px;padding:11px 16px;border-bottom:1px solid #1a4256}
.register .row{position:absolute;left:18px;font-size:9px;display:flex;align-items:center}
.register .row span{width:41px}
.register .row i{display:block;width:156px;height:19px;background:#fff;border-radius:4px}
.btn{position:absolute;font-size:9px;color:#5a2a00;background:linear-gradient(#ffc145,#f08a0c);border-radius:5px;text-align:center;line-height:18px;box-shadow:0 1px 2px rgba(0,0,0,.3)}
.btn.blue{color:#fff;background:linear-gradient(#43b1ef,#1775c4)}
.card{background:linear-gradient(#fff,#ececec);border:1px solid #ccd;border-radius:5px;box-shadow:0 3px 5px rgba(0,0,0,.12)}
.card h3{font-weight:400;font-size:13px;color:var(--link);margin:12px 12px 0;padding-bottom:6px;border-bottom:1px solid var(--line)}
.card .thumb{position:absolute;left:10px;top:48px;width:88px;height:78px;border-radius:5px;background:linear-gradient(135deg,#8a8f95,#e3e6e9 60%,#5d6f80)}
.card p{position:absolute;left:107px;top:48px;width:96px;font-size:9px;line-height:13.3px;text-align:justify}
.loc ul{list-style:none;margin:8px 0 0 11px}
.loc li{font-size:9px;height:17px;line-height:17px}
.docs .doc{position:absolute;left:8px;width:295px;height:50px;border:1px solid #d8dde0;background:#fff}
.doc b{position:absolute;left:13px;top:11px;font-weight:400;font-size:10.5px;color:var(--link)}
.doc small{position:absolute;left:15px;top:30px;font-size:8px;color:#555}
.pager{position:absolute;left:237px;top:432px;display:flex;gap:4px;font-size:8px;align-items:center}
.pager span{width:13px;height:12px;border:1px solid #999;background:#eee;text-align:center;line-height:11px}
.promo{left:611px;top:597px;width:223px;height:186px;background:linear-gradient(#c9e3f0,#f6fbfd 55%,#fff)}
.promo .badge{position:absolute;left:14px;top:6px;width:60px;height:56px;border-radius:50%;background:#5aa8df}
.promo .hd{position:absolute;left:86px;top:12px;font-size:13px;line-height:15px;color:var(--navy)}
.promo .hd em{font-style:normal;color:var(--red);font-size:16px;display:block}
.promo ol{position:absolute;left:15px;top:85px;font-size:10.5px;line-height:16.5px;list-style:none}
.promo .cta{position:absolute;left:0;bottom:0;width:223px;height:40px;background:linear-gradient(#e7262d,#b9151b);color:#fff;font-size:12px;line-height:40px;text-align:center}
.news{left:611px;top:797px;width:223px;height:109px;background:var(--teal);box-shadow:0 4px 6px rgba(0,0,0,.15)}
.news h4{font-family:"PT Sans Narrow",sans-serif;font-weight:400;font-size:13px;color:#fff;padding:12px 14px 8px;border-bottom:1px solid #2d6580}
.news .in{position:absolute;left:14px;top:48px;width:193px;height:23px;background:#fff;font-size:9px;line-height:23px;padding-left:9px;color:#333}
.footer{left:0;top:972px;width:961px;height:100px;background:linear-gradient(#dbe9f0,#fff);border-top:3px solid var(--teal)}
.banner{left:203px;top:992px;width:538px;height:66px;background:#262a2e}
.banner .badge{position:absolute;left:14px;top:6px;width:58px;height:52px;border-radius:50%;background:#5aa8df}
.banner .hd{position:absolute;left:87px;top:10px;font-size:13px;line-height:15px;color:#fff}
.banner .hd em{font-style:normal;color:var(--red);font-size:15px;display:block}
.banner ol{position:absolute;left:228px;top:9px;font-size:10px;line-height:16.5px;color:#ccc;list-style:none;border-left:1px solid #555;padding-left:9px}
.banner .cta{position:absolute;left:424px;top:8px;width:103px;height:51px;background:linear-gradient(#e7262d,#b9151b);border:1px solid #f55;border-radius:3px;color:#fff;font-size:12px;line-height:14.5px;text-align:center;padding-top:4px}
.flinks{left:0;top:1082px;width:921px;text-align:center;font-size:9px;color:#333}
.flinks span{margin:0 5px;color:#666}
.copy{left:0;top:1101px;width:921px;text-align:center;font-size:9px}
.rule{left:273px;top:1128px;width:380px;height:2px;background:#c8d3da}
.follow{left:0;top:1146px;width:921px;text-align:center;font-size:9px}
.social{left:425px;top:1164px;display:flex;gap:3px}
.social i{width:15px;height:15px;border-radius:2px}
</style>
</head>
<body>
<div class="page">
  <header class="abs header"></header>
  <div class="abs logo">BPP</div>
  <div class="abs topbar">
    <svg width="12" height="10" viewBox="0 0 12 10"><path d="M1 4c0-3 10-3 10 0l-2 1-1-2H4L3 5zM3 6h6l1 4H2z" fill="#333"/></svg>
    <span>call us now</span><span class="phone">415.XXX.XXXX</span><span class="sep"></span><span>Sign In</span><span class="sep"></span><span>Sign Up</span>
  </div>
  <div class="abs search"><i><svg width="10" height="10" viewBox="0 0 10 10"><circle cx="4" cy="4" r="3" stroke="#fff" fill="none" stroke-width="1.5"/><path d="M6 6l3 3" stroke="#fff" stroke-width="1.5"/></svg></i>Search</div>

  <nav class="abs nav">
    <a style="left:177px">Home</a><span class="div" style="left:240px"></span>
    <a style="left:289px">About Us</a><span class="div" style="left:348px"></span>
    <a style="left:407px">Services</a><span class="div" style="left:466px"></span>
    <a style="left:524px">Post Your Profile</a><span class="div" style="left:589px"></span>
    <a style="left:646px">Employers / Hospitals</a><span class="div" style="left:704px"></span>
    <a style="left:770px">Contact Us</a>
  </nav>

  <div class="abs hero" role="img" aria-label="Photo of a pediatrician with a smiling young patient"></div>
  <div class="abs arrow" style="left:130px"><svg width="10" height="14"><path d="M8 1L2 7l6 6" stroke="#2d6f95" stroke-width="2.5" fill="none"/></svg></div>
  <div class="abs arrow" style="left:801px"><svg width="10" height="14"><path d="M2 1l6 6-6 6" stroke="#2d6f95" stroke-width="2.5" fill="none"/></svg></div>

  <section class="abs register">
    <h2>Register Now</h2>
    <div class="row" style="top:51px"><span>Name</span><i></i></div>
    <div class="row" style="top:84px"><span>E mail</span><i></i></div>
    <div class="row" style="top:116px"><span>Phone</span><i></i></div>
    <div class="row" style="top:147px"><span>Country</span><i></i></div>
    <div class="row" style="top:179px"><span>Message</span><i></i></div>
    <div class="btn" style="left:158px;top:212px;width:58px">Submit</div>
  </section>

  <section class="abs card" style="left:130px;top:424px;width:215px;height:159px">
    <h3>About Us</h3>
    <div class="thumb" role="img" aria-label="Photo of doctors meeting in a clinic"></div>
    <p>Lorem Ipsum is simply dummy text of the printing and typeset-ting industry. Lorem Ipsum has been the industry's...</p>
    <div class="btn blue" style="left:149px;top:137px;width:56px">Read More</div>
  </section>
  <section class="abs card" style="left:358px;top:424px;width:215px;height:159px">
    <h3>Services</h3>
    <div class="thumb" role="img" aria-label="Photo of a business handshake"></div>
    <p>Lorem Ipsum is simply dummy text of the printing and typeset-ting industry. Lorem Ipsum has been the industry's...</p>
    <div class="btn blue" style="left:149px;top:137px;width:56px">Read More</div>
  </section>

  <section class="abs card loc" style="left:129px;top:597px;width:153px;height:365px">
    <h3 style="margin:10px 0 0;padding:0 10px 6px">Location Wise</h3>
    <ul>
      <li>Doctors in India</li><li>Doctors in USA</li><li>Doctors in Bangalore</li><li>Doctors in New York</li>
      <li>Doctors in Kolkata</li><li>Doctors in Texas</li><li>Doctors in Delhi</li><li>Doctors in Florida</li>
      <li>Doctors in Chandigarh</li><li>Doctors in Ohio</li><li>Doctors in Hyderabad</li><li>Doctors in New Jersey</li>
      <li>Doctors in Mumbai</li><li>Doctors in North Carolina</li><li>Doctors in Pune</li><li>Doctors in Massachusetts</li>
      <li>Doctors in Mangalore</li><li>Doctors in Indiana</li><li>Doctors in Surat</li>
    </ul>
  </section>

  <section class="abs card docs" style="left:289px;top:597px;width:314px;height:365px">
    <div class="doc" style="top:11px"><b>Dr. Priya Anand , Pediatrician</b><small>Cedar Park Lane, Riverton</small></div>
    <div class="doc" style="top:66px"><b>Dr. Nikhil Rao Menon , Pediatrician</b><small>Cedar Park Lane, Riverton</small></div>
    <div class="doc" style="top:121px"><b>Dr. Daniel Hart , Pediatrician</b><small>Cedar Park Lane, Riverton</small></div>
    <div class="doc" style="top:176px"><b>Dr. Ravi Sethna , Pediatrician</b><small>Cedar Park Lane, Riverton</small></div>
    <div class="doc" style="top:231px"><b>Dr. Karan Malhotra , Pediatrician</b><small>Cedar Park Lane, Riverton</small></div>
    <div class="doc" style="top:287px"><b>Dr. Alan Whitford , Pediatrician</b><small>Cedar Park Lane, Riverton</small></div>
    <div class="pager">◂<span>1</span><span>2</span><span>3</span><span>4</span>▸</div>
  </section>

  <aside class="abs promo">
    <div class="badge" role="img" aria-label="Cartoon mascot illustration"></div>
    <div class="hd"><em>Get 20% OFF</em>Your Next Theme<br>Template Purchase!</div>
    <ol><li>1. Order Theme 1.5, 1.6, 1.7, 2.5 Template</li><li>2. Receive a promocode to your email</li><li>3. Save 20% on your next purchase</li></ol>
    <div class="cta">Buy Theme 1.5, 1.6, 1.7, 2.5 Template</div>
  </aside>

  <section class="abs news">
    <h4>SIGN UP OUR NEWSLETTER</h4>
    <div class="in">Enter your email id</div>
    <div class="btn" style="left:155px;top:79px;width:53px">Sign Up</div>
  </section>

  <footer class="abs footer"></footer>
  <div class="abs banner">
    <div class="badge" role="img" aria-label="Cartoon mascot illustration"></div>
    <div class="hd"><em>Get 20% OFF</em>Your Next Theme<br>Template Purchase!</div>
    <ol><li>1. Order Theme 1.5, 1.6, 1.7, 2.5 Template</li><li>2. Receive a promocode to your email</li><li>3. Save 20% on your next purchase</li></ol>
    <div class="cta">Buy Theme<br>1.5, 1.6, 1.7, 2.5<br>Template Now</div>
  </div>
  <div class="abs flinks">Home<span>|</span>About Us<span>|</span>Services<span>|</span>Post Your Profile<span>|</span>Employers / Hospitals<span>|</span>Contact Us</div>
  <div class="abs copy">Copyrights @ 2012 All Rights Reserved</div>
  <div class="abs rule"></div>
  <div class="abs follow">Follow Us on</div>
  <div class="abs social"><i style="background:#3b5a9a"></i><i style="background:#1d73b0"></i><i style="background:#3aa5dd"></i><i style="background:#f08a1c"></i></div>
</div>
</body>
</html>
```